Construction material supplies company business card ****

1. Full company name “K T Masonry Works Ltd”
I am after a Business card design for the company as a whole. We are better known in Solomon Islands as “K T Masonry” for short.

We are a building materials supplier of
Ready Mixed Concrete, Bricks and Blocks,
Quarry products- gravel, aggregates, sand etc.
Cement distributor/retailer of reputable brands.
Other prefab concrete products. Culverts, wave breakers, concrete retaining blocks etc.

2. Competitive Advantage over Competition: Quality, efficient, professional, dependable, reliable

3. We want people to feel trust worthy, high quality, strong when they see our brand

5. No preference to color. Maybe more sturdy and corporate. Not fancy.

Industry/Entity Type

CONSTRUCTION SUPPLY

Contact Information for Business Card

Name, Position, office phone mob phone, email

Requirements
Must have
• the company logo
Nice to have
• would like to see a mixture of designs, of with logo only and also with simple graphic designs to bring out the company whilst still have the strong sturdy professional feeling

```html
<!DOCTYPE html>
<html lang="en">
<head>
<meta charset="utf-8">
<title>K T Masonry – Business Card</title>
<link rel="stylesheet" href="https://fonts.googleapis.com/css2?family=Saira:wght@700&family=Roboto:wght@400;700&display=swap">
<style>
  :root {
    --backdrop: #2b2b2b;
    --navy: #0f3559;
    --front-top: #34557c;
    --front-bottom: #284a70;
    --band: rgba(14, 44, 78, 0.72);
    --pill: rgba(25, 56, 92, 0.85);
    --pill-edge: rgba(160, 185, 215, 0.35);
    --light-text: #e9eef4;
    --back-paper: #e7e7e6;
  }
  * { margin: 0; padding: 0; box-sizing: border-box; }
  html, body {
    width: 1200px; height: 1138px; overflow: hidden;
    background: var(--backdrop);
  }
  .canvas { position: relative; width: 1200px; height: 1138px; }

  .card {
    position: absolute; width: 624px; height: 375px;
    border-radius: 16px; overflow: hidden;
  }

  /* Front */
  .card-front {
    left: 274px; top: 186px;
    background: linear-gradient(160deg, var(--front-top), var(--front-bottom));
    color: var(--light-text);
    font-family: "Roboto", sans-serif;
    text-align: center;
  }
  .front-wordmark {
    position: absolute; left: 0; right: 0; top: 62px;
    font-family: "Saira", sans-serif; font-weight: 700;
    font-size: 56px; letter-spacing: 2px; color: #f1f3f5;
    line-height: 1;
  }
  .supplier-pill {
    position: absolute; left: 138px; top: 184px; width: 346px; height: 41px;
    border-radius: 21px; background: var(--pill);
    border: 1px solid var(--pill-edge);
    font-size: 15px; line-height: 39px; z-index: 2;
  }
  .product-band {
    position: absolute; left: 0; right: 0; top: 214px; height: 78px;
    background: var(--band);
    padding-top: 22px; font-size: 15.5px; line-height: 22px;
  }
  .product-extra {
    position: absolute; left: 0; right: 0; top: 306px;
    font-size: 15.5px; line-height: 25px;
  }

  /* Back */
  .card-back {
    left: 276px; top: 608px;
    background: var(--back-paper);
    color: var(--navy);
    font-family: "Roboto", sans-serif;
  }
  .back-wordmark {
    position: absolute; left: 30px; top: 50px;
    font-family: "Saira", sans-serif; font-weight: 700;
    font-size: 31px; letter-spacing: 1px; line-height: 1;
  }
  .person-name {
    position: absolute; left: 30px; top: 140px;
    font-size: 23px; font-weight: 700;
  }
  .person-role {
    position: absolute; left: 30px; top: 170px; font-size: 16px;
  }
  .contact-list { position: absolute; left: 30px; top: 216px; list-style: none; }
  .contact-list li {
    display: flex; align-items: center; height: 26px; font-size: 16px;
  }
  .contact-list svg { width: 14px; height: 14px; margin-right: 18px; fill: var(--navy); }
  .address {
    position: absolute; left: 30px; top: 298px;
    font-size: 16px; line-height: 26px; font-style: normal;
  }
</style>
</head>
<body>
<main class="canvas">

  <section class="card card-front" aria-label="Business card front">
    <div class="front-wordmark">K T MASONRY</div>
    <div class="supplier-pill">We are a building materials supplier of</div>
    <div class="product-band">
      <p>Ready Mixed Concrete, Bricks and Blocks, Quarry Products</p>
      <p>Quarry Products:- Gravel, Aggregates, Sand Etc.</p>
    </div>
    <div class="product-extra">
      <p>Cement Distributor/Retailer of Reputable Brands.</p>
      <p>Other Concrete Products Culverts, Wave Breakers, Concrete Retaining Blocks</p>
    </div>
  </section>

  <section class="card card-back" aria-label="Business card back">
    <div class="back-wordmark">K T MASONRY</div>
    <h1 class="person-name">Daniel Hartley</h1>
    <p class="person-role">Managing Director</p>
    <ul class="contact-list">
      <li>
        <svg viewBox="0 0 16 16" aria-hidden="true"><path d="M1 5c0-2 3-3 7-3s7 1 7 3v1h-4V4.5H5V6H1z M3 7h10l1 7H2z M8 8.5a2 2 0 1 0 0 4a2 2 0 1 0 0-4z"/></svg>
        000 0000 0000
      </li>
      <li>
        <svg viewBox="0 0 16 16" aria-hidden="true"><path d="M1 3h14v10H1z M2.5 4.5v.4L8 9l5.5-4.1v-.4z" fill-rule="evenodd"/></svg>
        daniel@ktmasonry.com
      </li>
      <li>
        <svg viewBox="0 0 16 16" aria-hidden="true"><path d="M8 1a7 7 0 1 0 0 14A7 7 0 1 0 8 1zm0 1.5c.9 0 1.8 2 2 4.7H6c.2-2.7 1.1-4.7 2-4.7zM2.6 7.2h2.1c.1-1.6.4-3 .9-4a5.6 5.6 0 0 0-3 4zm8.7 0h2.1a5.6 5.6 0 0 0-3-4c.5 1 .8 2.4.9 4zM2.6 8.8a5.6 5.6 0 0 0 3 4c-.5-1-.8-2.4-.9-4zm3.4 0c.2 2.7 1.1 4.7 2 4.7s1.8-2 2-4.7zm5.3 0c-.1 1.6-.4 3-.9 4a5.6 5.6 0 0 0 3-4z"/></svg>
        www.ktmasonry.com
      </li>
    </ul>
    <address class="address">234 Anywhere St., Any City,<br>Any Town, US 123456</address>
  </section>

</main>
</body>
</html>
```